Webshop for furniture and lamps

We need a design for a web shop with APP that should have two options:
1-Webshop in general which should attract to private customer in general and
2-Website that is meant to attract big customers as hotels and restaurants who would have their own customerize login.

That's the idea behind the shop.

It should be diveded into 4 parts
vintage furniture
rattan set outdoor and indoor
lamps and
wooden wall decor

The name of the shop is loma vereda!

Please kindly make me an offer.

Reason: Dear designers, so far there hasn't been a design that really matched. Look up German web sites like www.glimmerhof-wohnen.de or www.sitzraum77.de... Haven't been convinced by designs! Sorry folks. Please submit some new ones. Kind regards Ned

```html
<!DOCTYPE html>
<html lang="en">
<head>
<meta charset="utf-8">
<title>loma vereda – furniture and lamps</title>
<link rel="stylesheet" href="https://fonts.googleapis.com/css2?family=PT+Sans:wght@400;700&family=Open+Sans:wght@400;600;700&display=swap">
<style>
:root{
  --orange:#e5801f;
  --orange-dark:#c86a12;
  --ink:#3a3a3a;
  --ink-soft:#777;
  --line:#dcdcdc;
  --page:#ececec;
  --panel:#ffffff;
  --topbar:#2f2f2f;
  --footer:#3b2f27;
  --footer-deep:#2a221c;
  --modal:#4a4a4a;
  --veil:rgba(0,0,0,.62);
  --wood-a:#8a5a36;
  --wood-b:#5e3b22;
}
*{box-sizing:border-box;margin:0;padding:0}
html,body{width:1200px;height:2588px;overflow:hidden}
body{position:relative;background:var(--page);font-family:"Open Sans",Arial,sans-serif;color:var(--ink);font-size:12px}
.abs{position:absolute}
.photo{position:absolute}
h2.block-title{font-family:"PT Sans",Arial,sans-serif;font-weight:700;font-size:19px;text-transform:uppercase;color:var(--ink);letter-spacing:.3px}
.panel{position:absolute;background:var(--panel)}

/* top bar */
.topbar{left:0;top:0;width:1200px;height:39px;background:var(--topbar);color:#ccc;font-size:12px}
.topbar .welcome{left:93px;top:12px}
.topbar .tools{right:90px;top:12px;display:flex;gap:26px}

/* header */
.header{left:0;top:39px;width:1200px;height:147px;background:var(--page)}
.brand{left:93px;top:46px;display:flex;align-items:center;gap:10px}
.brand .mark{width:28px;height:28px;background:var(--ink)}
.brand .name{font-family:"PT Sans",sans-serif;font-weight:700;font-size:28px;color:var(--orange);text-transform:uppercase}
.nav{left:440px;top:60px;display:flex;gap:30px;font-family:"PT Sans",sans-serif;font-weight:700;font-size:14px}
.search{left:928px;top:58px;width:183px;height:24px;border-bottom:1px solid var(--line);font-size:10px;color:#999;padding:5px 6px}
.search svg{position:absolute;right:4px;top:6px}

/* hero */
.hero{left:93px;top:186px;width:1016px;height:354px;background:linear-gradient(100deg,#b7a690 0%,#d7cbbb 35%,#8e7c68 70%,#6d5c4c 100%)}
.hero-title{left:939px;top:252px;font-family:"PT Sans",sans-serif;font-weight:700;font-size:38px;color:#fff}
.hero-copy{left:939px;top:336px;width:160px;font-size:12px;line-height:21px;color:#fff}
.hero-btn{left:859px;top:460px;width:95px;height:30px;border:1px solid #fff;color:#fff;font-size:11px;text-align:center;line-height:28px}

/* sidebar */
.cat-list{list-style:none;margin-top:22px;font-size:10px;text-transform:uppercase;color:#555}
.cat-list li{margin-bottom:22px}
.cat-list li.active{font-weight:700}

/* product cards */
.card{position:absolute;text-align:center}
.card .badge{position:absolute;left:12px;top:0;padding:3px 8px;background:#9a9a9a;color:#fff;font-size:10px}
.card .badge.hot{background:var(--orange)}
.card .pic{margin:0 auto}
.card .title{font-family:"PT Sans",sans-serif;font-weight:700;font-size:11px;text-transform:uppercase;margin-top:14px}
.card .rule{width:40px;height:2px;background:var(--orange);margin:6px auto 8px}
.card .desc{font-size:8px;line-height:11px;color:var(--ink-soft);width:160px;margin:0 auto}
.price{display:inline-flex;margin-top:14px;height:30px}
.price .amount{width:78px;border:1px solid var(--line);color:var(--orange);font-weight:700;font-size:12px;line-height:28px}
.price .cart{width:34px;background:#8b8b8b;display:flex;align-items:center;justify-content:center}

.section-filters{position:absolute;right:12px;top:18px;font-size:10px;color:#888}
.section-filters b{color:#333;font-weight:600}
.arrows{position:absolute;display:flex;gap:4px}
.arrows span{width:26px;height:24px;background:#ddd}

/* blog / tweets / video */
.post h3{font-family:"PT Sans",sans-serif;font-size:11px;font-weight:700;text-transform:uppercase;margin-top:16px}
.post .date{font-size:8px;color:#999;margin:3px 0 10px}
.post p{font-size:8px;line-height:11px;color:var(--ink-soft)}
.post .more{font-size:8px;color:#888;margin-top:10px}
.tweet{position:absolute;left:0;display:flex;gap:22px}
.tweet .bird{width:40px;height:40px;border-radius:50%;background:var(--orange)}
.tweet .txt{font-size:8px;line-height:11px;color:var(--ink-soft);width:200px}
.tweet .txt b{color:#333}
.tweet .txt span{color:var(--orange)}

/* footer */
.footer{left:0;top:2300px;width:1200px;height:220px;background:linear-gradient(90deg,var(--footer),#463629 50%,var(--footer))}
.fcol{position:absolute;top:48px;color:#c9bfb6;font-size:11px}
.fcol h4{font-family:"PT Sans",sans-serif;font-size:13px;color:#fff;text-transform:uppercase;margin-bottom:14px}
.fcol li{list-style:none;margin-bottom:10px}
.news-form{display:flex;margin-top:24px}
.news-form .field{width:166px;height:30px;border:1px solid #aaa;font-size:10px;color:#bbb;padding:8px 12px}
.news-form .go{width:82px;height:30px;background:#e9e4df;color:#333;font-weight:700;font-size:11px;text-align:center;line-height:30px}
.dots{display:flex;gap:7px}
.dots span{width:20px;height:20px;border-radius:50%;background:#ddd}
.cards-row{display:flex;gap:7px}
.cards-row span{width:32px;height:18px;background:#ddd}
.bottombar{left:0;top:2520px;width:1200px;height:68px;background:var(--footer-deep);color:#bbb;font-size:11px}
.bottombar .copy{left:88px;top:26px}
.bottombar .links{right:88px;top:26px;display:flex;gap:22px}

/* overlay + modal */
.veil{left:0;top:0;width:1200px;height:2300px;background:var(--veil)}
.veil-foot{left:0;top:2300px;width:1200px;height:288px;background:rgba(0,0,0,.25)}
.modal{left:259px;top:142px;width:682px;height:346px;background:var(--modal)}
.modal .side{position:absolute;left:0;top:0;width:341px;height:346px;background:radial-gradient(circle at 40% 40%,#a0744a,#6b4526 70%,#4e321c)}
.members{position:absolute;left:0;top:100px;width:341px;text-align:center;color:#fff}
.members .icon{width:50px;height:50px;border-radius:50%;background:#fff;margin:0 auto;display:flex;align-items:center;justify-content:center}
.members h3{font-family:"PT Sans",sans-serif;font-size:17px;margin:6px 0 8px}
.members p{font-size:9px;line-height:13px;width:170px;margin:0 auto}
.signup{position:absolute;left:412px;top:76px;width:197px;height:173px;background:var(--orange);text-align:center;color:#fff;padding:12px 10px}
.signup h3{font-family:"PT Sans",sans-serif;font-size:12px}
.signup .note{font-size:6px;margin:3px 0 7px}
.signup .input{height:19px;background:#fff;color:#aaa;font-size:6px;line-height:19px;margin-bottom:7px}
.signup .submit{height:24px;background:#3a3a3a;font-size:9px;font-weight:700;line-height:24px;margin-bottom:7px}
.signup .fine{font-size:6px;line-height:8px}
.close{left:916px;top:113px;width:22px;height:22px;border-radius:50%;background:#fff;border:2px solid #444}
</style>
</head>
<body>

<div class="abs topbar">
  <div class="abs welcome">Mara Lindqvist, welcome to our online store!</div>
  <div class="abs tools"><span>⚙ Setting ▾</span><span>My Account ▾</span><span>Cart: 0 item</span></div>
</div>

<header class="abs header">
  <div class="abs brand"><span class="mark"></span><span class="name">loma vereda</span></div>
  <nav class="abs nav"><span>HOME</span><span>CATEGORIES</span><span>ABOUT US</span><span>FAQs</span><span>CONTACT US</span></nav>
  <div class="abs search">search your idea here
    <svg width="12" height="12" viewBox="0 0 12 12"><circle cx="5" cy="5" r="3.5" fill="none" stroke="#999" stroke-width="1.4"/><path d="M8 8l3 3" stroke="#999" stroke-width="1.4"/></svg>
  </div>
</header>

<div class="photo hero" role="img" aria-label="Living room interior with armchair and wooden wall decor"></div>
<div class="abs hero-title">SUMEI</div>
<div class="abs hero-copy">Sed ut perspiciatis unde omnis iste natus error sit voluptatem accusantium dolor sit</div>
<div class="abs hero-btn">SHOP NOW</div>

<!-- shop by category -->
<aside class="panel" style="left:93px;top:568px;width:233px;height:209px;padding:18px 14px">
  <h2 class="block-title">Shop by category</h2>
  <ul class="cat-list">
    <li>Vintage furniture</li>
    <li class="active">Rattan set outdoor and indoor</li>
    <li>Lamps and</li>
    <li>Wooden wall decor</li>
  </ul>
</aside>

<!-- promo -->
<section class="panel" style="left:354px;top:568px;width:755px;height:269px">
  <div class="abs" style="left:21px;top:12px;padding:10px 12px;background:var(--orange);color:#fff;font-family:'PT Sans',sans-serif;font-weight:700;font-size:17px;text-transform:uppercase">Promo of the month</div>
  <div class="abs" style="left:40px;top:90px;width:180px;text-align:center">
    <div style="font-family:'PT Sans',sans-serif;font-weight:700;font-size:13px">VOLUPTATEM FUGIT AUT</div>
    <div style="color:var(--orange);font-weight:700;font-size:17px;margin-top:8px">$380.00</div>
    <p style="font-size:8px;line-height:11px;color:var(--ink-soft);margin-top:8px">Ut enim ad minima veniam quis nostrum exercitationem ullam corporis suscipit laboriosam nisi</p>
    <div style="display:inline-block;margin-top:18px;padding:8px 18px;border:1px solid #bbb;font-size:11px">READ MORE</div>
  </div>
  <div class="photo" role="img" aria-label="Vintage painted wooden cabinet with open door" style="left:336px;top:32px;width:303px;height:231px;background:linear-gradient(135deg,#7a5234,#5a3a24 60%,#8a6a4a)"></div>
  <div class="arrows" style="left:680px;top:4px"><span></span><span></span></div>
</section>

<!-- best seller -->
<aside class="panel" style="left:93px;top:863px;width:233px;height:518px">
  <h2 class="block-title abs" style="left:12px;top:18px">Best seller</h2>
  <div class="card" style="left:0;top:80px;width:233px">
    <div class="photo" role="img" aria-label="Round rattan table set" style="position:relative;width:130px;height:100px;margin:0 auto;background:radial-gradient(ellipse,#a8754a,#6f4a2c)"></div>
    <div class="title">Voluptatem fugit aut</div><div class="rule"></div>
    <div class="price"><span class="amount">$858.00</span><span class="cart"><svg width="16" height="14" viewBox="0 0 16 14"><path d="M1 1h3l2 8h8l2-6H5" fill="none" stroke="#fff" stroke-width="1.5"/><circle cx="7" cy="12" r="1.3" fill="#fff"/><circle cx="13" cy="12" r="1.3" fill="#fff"/></svg></span></div>
  </div>
  <div class="card" style="left:0;top:324px;width:233px">
    <div class="photo" role="img" aria-label="Vintage wooden chest" style="position:relative;width:130px;height:86px;margin:0 auto;background:linear-gradient(135deg,#8a6248,#5e4030)"></div>
    <div class="title">Voluptatem fugit aut</div><div class="rule"></div>
    <div class="price"><span class="amount">$858.00</span><span class="cart"><svg width="16" height="14" viewBox="0 0 16 14"><path d="M1 1h3l2 8h8l2-6H5" fill="none" stroke="#fff" stroke-width="1.5"/><circle cx="7" cy="12" r="1.3" fill="#fff"/><circle cx="13" cy="12" r="1.3" fill="#fff"/></svg></span></div>
  </div>
</aside>

<!-- new product -->
<section class="panel" style="left:354px;top:863px;width:755px;height:384px">
  <h2 class="block-title abs" style="left:12px;top:18px">New product</h2>
  <div class="section-filters">Vintage Furniture &nbsp;|&nbsp; <b>Rattan Set Outdoor and Indoor</b> &nbsp;|&nbsp; Lamps &nbsp;|&nbsp; Wooden Wall Decor</div>
  <div class="card" style="left:0;top:70px;width:251px">
    <span class="badge">NEW</span>
    <div class="photo" role="img" aria-label="Painted chest of drawers" style="position:relative;width:130px;height:140px;margin:0 auto;background:linear-gradient(135deg,#8a4b3c,#4f5e52 55%,#6a3c30)"></div>
    <div class="title">Voluptatem fugit aut</div><div class="rule"></div>
    <p class="desc">Ut enim ad minima veniam quis nostrum exercitationem ullam corporis</p>
    <div class="price"><span class="amount">$858.00</span><span class="cart"><svg width="16" height="14" viewBox="0 0 16 14"><path d="M1 1h3l2 8h8l2-6H5" fill="none" stroke="#fff" stroke-width="1.5"/><circle cx="7" cy="12" r="1.3" fill="#fff"/><circle cx="13" cy="12" r="1.3" fill="#fff"/></svg></span></div>
  </div>
  <div class="card" style="left:252px;top:70px;width:251px">
    <span class="badge hot">-10%</span>
    <div class="photo" role="img" aria-label="Painted wooden trunk" style="position:relative;width:150px;height:140px;margin:0 auto;background:linear-gradient(180deg,#ececec 20%,#8e6a4c 22%,#6d4e36 80%,#ececec 82%)"></div>
    <div class="title">Voluptatem fugit aut</div><div class="rule"></div>
    <p class="desc">Ut enim ad minima veniam quis nostrum exercitationem ullam corporis</p>
    <div class="price"><span class="amount">$858.00</span><span class="cart"><svg width="16" height="14" viewBox="0 0 16 14"><path d="M1 1h3l2 8h8l2-6H5" fill="none" stroke="#fff" stroke-width="1.5"/><circle cx="7" cy="12" r="1.3" fill="#fff"/><circle cx="13" cy="12" r="1.3" fill="#fff"/></svg></span></div>
  </div>
  <div class="card" style="left:504px;top:70px;width:251px">
    <span class="badge">NEW</span>
    <div class="photo" role="img" aria-label="Grey rattan round table with stools" style="position:relative;width:160px;height:140px;margin:0 auto;background:radial-gradient(ellipse at 50% 40%,#6a6a6a,#3c3c3c 70%,#ececec 72%)"></div>
    <div class="title">Voluptatem fugit aut</div><div class="rule"></div>
    <p class="desc">Ut enim ad minima veniam quis nostrum exercitationem ullam corporis</p>
    <div class="price"><span class="amount">$858.00</span><span class="cart"><svg width="16" height="14" viewBox="0 0 16 14"><path d="M1 1h3l2 8h8l2-6H5" fill="none" stroke="#fff" stroke-width="1.5"/><circle cx="7" cy="12" r="1.3" fill="#fff"/><circle cx="13" cy="12" r="1.3" fill="#fff"/></svg></span></div>
  </div>
</section>

<!-- featured -->
<section class="panel" style="left:354px;top:1277px;width:755px;height:428px">
  <h2 class="block-title abs" style="left:12px;top:18px">Featured products</h2>
  <div class="section-filters">Vintage Furniture &nbsp;|&nbsp; Rattan Set Outdoor and Indoor &nbsp;|&nbsp; Lamps &nbsp;|&nbsp; Wooden Wall Decor</div>
  <div class="card" style="left:0;top:66px;width:251px">
    <span class="badge">NEW</span>
    <div class="photo" role="img" aria-label="Round rattan lounge set" style="position:relative;width:180px;height:150px;margin:0 auto;background:radial-gradient(ellipse,#a8754a,#6f4a2c 65%,#ececec 70%)"></div>
    <div class="title">Voluptatem fugit aut</div><div class="rule"></div>
    <p class="desc">Ut enim ad minima veniam quis nostrum exercitationem ullam corporis</p>
    <div class="price"><span class="amount">$858.00</span><span class="cart"><svg width="16" height="14" viewBox="0 0 16 14"><path d="M1 1h3l2 8h8l2-6H5" fill="none" stroke="#fff" stroke-width="1.5"/><circle cx="7" cy="12" r="1.3" fill="#fff"/><circle cx="13" cy="12" r="1.3" fill="#fff"/></svg></span></div>
  </div>
  <div class="card" style="left:252px;top:66px;width:251px">
    <div class="photo" role="img" aria-label="Vintage wooden side table" style="position:relative;width:160px;height:150px;margin:0 auto;background:linear-gradient(180deg,#ececec 25%,#7a4a36 28%,#5a3c2e 75%,#ececec 78%)"></div>
    <div class="title">Voluptatem fugit aut</div><div class="rule"></div>
    <p class="desc">Ut enim ad minima veniam quis nostrum exercitationem ullam corporis</p>
    <div class="price"><span class="amount">$858.00</span><span class="cart"><svg width="16" height="14" viewBox="0 0 16 14"><path d="M1 1h3l2 8h8l2-6H5" fill="none" stroke="#fff" stroke-width="1.5"/><circle cx="7" cy="12" r="1.3" fill="#fff"/><circle cx="13" cy="12" r="1.3" fill="#fff"/></svg></span></div>
  </div>
  <div class="card" style="left:504px;top:66px;width:251px">
    <span class="badge">NEW</span>
    <div class="photo" role="img" aria-label="Floor lamp with cream shade" style="position:relative;width:90px;height:150px;margin:0 auto;background:linear-gradient(180deg,#e9d8b4 0%,#d6bf92 35%,#a88650 40%,#8a6a3c 100%)"></div>
    <div class="title">Voluptatem fugit aut</div><div class="rule"></div>
    <p class="desc">Ut enim ad minima veniam quis nostrum exercitationem ullam corporis</p>
    <div class="price"><span class="amount">$858.00</span><span class="cart"><svg width="16" height="14" viewBox="0 0 16 14"><path d="M1 1h3l2 8h8l2-6H5" fill="none" stroke="#fff" stroke-width="1.5"/><circle cx="7" cy="12" r="1.3" fill="#fff"/><circle cx="13" cy="12" r="1.3" fill="#fff"/></svg></span></div>
  </div>
  <div class="abs" style="left:0;top:387px;width:755px;height:41px;background:#555;color:#fff;text-align:center;line-height:41px;font-size:11px">VIEW MORE ITEMS</div>
</section>

<!-- special offer -->
<aside class="panel" style="left:93px;top:1407px;width:233px;height:393px">
  <h2 class="block-title abs" style="left:12px;top:18px">Special offer</h2>
  <div class="arrows" style="left:162px;top:14px"><span></span><span></span></div>
  <div class="card" style="left:0;top:82px;width:233px">
    <div class="photo" role="img" aria-label="Tall painted vintage cabinet" style="position:relative;width:96px;height:205px;margin:0 auto;background:linear-gradient(180deg,#6a4a3a,#4a5a52 40%,#7a4a36 80%,#5a3a2a)"></div>
    <div class="title">Voluptatem fugit aut</div><div class="rule"></div>
    <p class="desc">Ut enim ad minima veniam quis nostrum exercitationem</p>
    <div class="price" style="margin-top:10px"><span class="amount">$858.00</span><span class="cart"><svg width="16" height="14" viewBox="0 0 16 14"><path d="M1 1h3l2 8h8l2-6H5" fill="none" stroke="#fff" stroke-width="1.5"/><circle cx="7" cy="12" r="1.3" fill="#fff"/><circle cx="13" cy="12" r="1.3" fill="#fff"/></svg></span></div>
  </div>
</aside>

<!-- outdoor banner -->
<div class="photo" role="img" aria-label="Striped outdoor lounge sofas" style="left:354px;top:1731px;width:755px;height:125px;background:linear-gradient(90deg,#b79a72,#d8c7a4 30%,#8c6d4c 60%,#5c4636)"></div>
<div class="abs" style="left:870px;top:1750px;color:#fff">
  <div style="font-family:'PT Sans',sans-serif;font-weight:700;font-size:26px;color:#f1e6d6">outside furniture</div>
  <div style="font-size:12px;color:#eee">big savings on quality items</div>
  <div style="font-size:10px;margin-top:14px;margin-left:46px">view the collection</div>
</div>

<!-- blog / tweets / video -->
<section class="panel" style="left:93px;top:1882px;width:1016px;height:362px">
  <div class="abs" style="left:14px;top:18px;width:300px">
    <h2 class="block-title">Lates from blog</h2>
    <div class="arrows" style="left:240px;top:-4px"><span></span><span></span></div>
    <div class="post">
      <h3>Lorem ipsum dolor sit amet rem eos</h3>
      <div class="date">May 10, 2014</div>
      <p>Lorem ipsum dolor sit amet consectetur adipiscing elit sed do eiusmod tempor incididunt ut labore et dolore magna aliqua ut enim ad minim veniam quis nostrud</p>
      <div class="more">read more</div>
    </div>
    <div class="post">
      <h3>Lorem ipsum dolor sit amet rem eos</h3>
      <div class="date">May 10, 2014</div>
      <p>Lorem ipsum dolor sit amet consectetur adipiscing elit sed do eiusmod tempor incididunt ut labore et dolore magna aliqua ut enim ad minim veniam quis nostrud</p>
      <div class="more">read more</div>
    </div>
  </div>
  <div class="abs" style="left:348px;top:18px;width:320px;height:320px">
    <h2 class="block-title">Tweets</h2>
    <div class="tweet" style="top:50px"><span class="bird"></span><div class="txt"><b>Lina Rios</b> <span>@linarios</span><br>New rattan lounge set just arrived in store, perfect for terraces and garden cafés<br><br>retweeted by <b>Loma Vereda</b></div></div>
    <div class="tweet" style="top:150px"><span class="bird"></span><div class="txt"><b>Lina Rios</b> <span>@linarios</span><br>New rattan lounge set just arrived in store, perfect for terraces and garden cafés<br><br>retweeted by <b>Loma Vereda</b></div></div>
    <div class="tweet" style="top:250px"><span class="bird"></span><div class="txt"><b>Lina Rios</b> <span>@linarios</span><br>New rattan lounge set just arrived in store, perfect for terraces and garden cafés<br><br>retweeted by <b>Loma Vereda</b></div></div>
  </div>
  <div class="abs" style="left:688px;top:18px">
    <h2 class="block-title">Watch our video</h2>
    <div class="photo" role="img" aria-label="Video still of a wooden coffee table in a living room" style="left:0;top:36px;width:313px;height:280px;background:linear-gradient(160deg,#cfc8be,#8a7868 55%,#5e4a3c)"></div>
    <svg class="abs" style="left:133px;top:153px" width="46" height="46" viewBox="0 0 46 46"><circle cx="23" cy="23" r="22" fill="#fff" opacity=".85"/><path d="M18 14l13 9-13 9z" fill="#555"/></svg>
  </div>
</section>

<div class="panel" style="left:93px;top:2262px;width:1016px;height:38px"></div>

<!-- footer -->
<footer class="abs footer">
  <div class="fcol" style="left:93px"><h4>Company</h4><ul><li>Search</li><li>About</li><li>News</li><li>Retailers</li><li>Contact Us</li></ul></div>
  <div class="fcol" style="left:265px"><h4>Shipping</h4><ul><li>Shipping Fee</li><li>Order and Returns</li><li>Track Order</li><li>Search Term</li><li>Site Map</li></ul></div>
  <div class="fcol" style="left:440px"><h4>FAQs</h4><ul><li>Customers Service</li><li>Privacy Policy</li><li>Term and Use</li><li>My Account</li><li>Others</li></ul></div>
  <div class="fcol" style="left:613px;width:300px"><h4>News &amp; Updates</h4>
    <div>Sign up to get the latest on sales, new releases and more …</div>
    <div class="news-form"><span class="field">enter your email here</span><span class="go">SIGN UP</span></div>
  </div>
  <div class="fcol" style="left:960px;width:150px"><h4>Follow us now</h4>
    <div class="dots"><span></span><span></span><span></span><span></span><span></span></div>
    <div style="height:1px;background:#8a7c70;margin:14px 0"></div>
    <h4 style="margin-bottom:10px">Payment method</h4>
    <div class="cards-row"><span></span><span></span><span></span><span></span></div>
  </div>
</footer>
<div class="abs bottombar">
  <div class="abs copy">© 2014 <b style="color:#fff">Loma Vereda</b></div>
  <div class="abs links"><span>About us</span><span>privacy policy</span><span>terms and use</span><span>Careers</span><span>Countries</span><span>contact us</span></div>
</div>

<!-- member sign-up overlay -->
<div class="abs veil"></div>
<div class="abs veil-foot"></div>
<div class="abs modal">
  <div class="side" role="img" aria-label="Rattan and driftwood decor texture"></div>
  <div class="members">
    <div class="icon"><svg width="26" height="26" viewBox="0 0 26 26"><circle cx="13" cy="9" r="5" fill="#6b4526"/><path d="M3 25c1-7 5-10 10-10s9 3 10 10z" fill="#6b4526"/></svg></div>
    <h3>MEMBERS</h3>
    <p>Create your own account and <b>SIGN IN</b> to get special offers for hotels and restaurants, discounts up to <b>50% off</b> every week</p>
    <p style="margin-top:10px">learn more</p>
  </div>
  <div class="signup">
    <h3>SIGN UP HERE</h3>
    <div class="note">Join us and get your business offers and latest deals</div>
    <div class="input">Your Name</div>
    <div class="input">Your Email Address</div>
    <div class="submit">SIGN UP</div>
    <div class="fine">Enter your details below to receive members prices</div>
  </div>
</div>
<div class="abs close"></div>
<svg class="abs" style="left:922px;top:119px" width="10" height="10" viewBox="0 0 10 10"><path d="M1 1l8 8M9 1l-8 8" stroke="#444" stroke-width="2"/></svg>

</body>
</html>
```